Business card design for new eCommerce site focusing on integrity and strong businsess tactics

We need a business card that will stand out and be memorable. Something with color that matches our company logo colors. Think high end version of Pactivo. There are 2 logos provided. The parent company is called Amber Ledge Partners and we are presenting a new and very exciting eCommerce site called BrightHarborTrade.example.

Target Market(s)

Our target markets are in the Activities, Food and Beverage, Health and Beauty

Industry/Entity Type

Marketing

Contact Information for Business Card

We have 4 members that need cards...I will provide all info to the winner of the design contest
Business Address is
4870 West 63rd Avenue, Suite C207
Phoenix AZ 85731

Font styles to use
Serif
Sans Serif

Colors

Designer to choose colors to be used in the design.

Requirements
Must have
• The card must be memorable...should be unique in design but must exude integrity and be playful .
• I have provided several colors or our parent company...please feel free to use which ever
Nice to have
• I will leave this up to you. Feel free to use other images of your choosing that wraps around our client.....Activities, Dining, Health, Beauty
Should not have
• just dont be boring

```html
<!DOCTYPE html>
<html lang="en">
<head>
<meta charset="utf-8">
<title>Amber Ledge Partners – Business Card</title>
<link href="https://fonts.googleapis.com/css2?family=Cabin:wght@400;500;700&display=swap" rel="stylesheet">
<style>
  :root {
    --blue: #2b7db0;
    --green: #8cc63f;
    --green-soft: #a6c94a;
    --white: #fbfbfb;
    --ink-light: #ffffff;
    --stage: #e9e9e9;
  }
  * { box-sizing: border-box; margin: 0; padding: 0; }
  html, body { width: 1200px; height: 960px; overflow: hidden; }
  body {
    background: var(--stage);
    font-family: "Cabin", Arial, sans-serif;
    position: relative;
  }
  .card {
    position: absolute;
    width: 600px;
    height: 343px;
    border-radius: 22px;
    overflow: hidden;
  }
  .card--front { left: 302px; top: 130px; background: var(--white); }
  .card--back { left: 299px; top: 490px; background: var(--blue); }

  .front-shape { position: absolute; inset: 0; }

  .brand {
    position: absolute;
    left: 270px;
    top: 74px;
    display: flex;
    align-items: center;
    gap: 10px;
  }
  .brand__dot { width: 26px; height: 26px; border-radius: 50%; background: var(--blue); }
  .brand__name { color: var(--green); font-weight: 500; font-size: 22px; }

  .contact { position: absolute; left: 28px; top: 140px; color: var(--ink-light); }
  .contact__name { color: var(--green); font-size: 24px; font-weight: 500; letter-spacing: -0.3px; line-height: 1.1; }
  .contact__role { font-size: 16px; line-height: 1.3; margin-bottom: 10px; }
  .contact__address { font-size: 14.5px; line-height: 1.3; margin-bottom: 9px; }
  .contact__list { list-style: none; font-size: 14.5px; line-height: 19.5px; }
  .contact__list li { display: flex; align-items: center; gap: 8px; }
  .contact__list svg { width: 13px; height: 13px; fill: var(--green); flex: none; }

  .back-mark {
    position: absolute;
    left: 50%;
    top: 72px;
    width: 140px;
    height: 140px;
    margin-left: -70px;
    border-radius: 50%;
    background: var(--green-soft);
  }
  .back-name {
    position: absolute;
    left: 0; right: 0;
    top: 222px;
    text-align: center;
    color: var(--green-soft);
    font-weight: 700;
    font-size: 34px;
  }
</style>
</head>
<body>

<section class="card card--front">
  <svg class="front-shape" viewBox="0 0 600 343" width="600" height="343">
    <path d="M0,0 H197 C225,150 330,285 458,343 H0 Z" fill="var(--blue)"/>
    <path d="M197,0 C225,150 330,285 458,343 C342,290 240,160 204,0 Z" fill="var(--green)"/>
  </svg>

  <div class="brand">
    <span class="brand__dot"></span>
    <span class="brand__name">BrightHarborTrade.example</span>
  </div>

  <div class="contact">
    <h1 class="contact__name">MARCUS HALE</h1>
    <p class="contact__role">CEO/FOUNDER</p>
    <p class="contact__address">4870 West 63rd Avenue<br>Suite C207, Phoenix AZ 85731</p>
    <ul class="contact__list">
      <li><svg viewBox="0 0 16 16"><path d="M3.5 1 L6 1 L7 4.5 L5.3 6 C6.2 8 8 9.8 10 10.7 L11.5 9 L15 10 L15 12.5 C15 13.9 13.9 15 12.5 15 C6.2 15 1 9.8 1 3.5 C1 2.1 2.1 1 3.5 1 Z"/></svg>555 210 4837</li>
      <li><svg viewBox="0 0 16 16"><path d="M4 0 H12 A1.5 1.5 0 0 1 13.5 1.5 V14.5 A1.5 1.5 0 0 1 12 16 H4 A1.5 1.5 0 0 1 2.5 14.5 V1.5 A1.5 1.5 0 0 1 4 0 Z M4.3 2 V12.5 H11.7 V2 Z M8 13.3 A0.9 0.9 0 1 0 8 15.1 A0.9 0.9 0 1 0 8 13.3 Z"/></svg>555 382 9061</li>
      <li><svg viewBox="0 0 16 16"><path d="M1 3 H15 V4 L8 9 L1 4 Z M1 5.5 L8 10.5 L15 5.5 V13 H1 Z"/></svg>marcus@brightharbortrade.example</li>
      <li><svg viewBox="0 0 16 16"><path d="M8 1 A7 7 0 1 0 8 15 A7 7 0 1 0 8 1 Z M4 4 L7 5 L6.5 8 L9 9.5 L8 13 L5 10 L3.5 6 Z M10 3 L12.5 5 L12 8 L10.5 6.5 Z"/></svg>www.brightharbortrade.example</li>
    </ul>
  </div>
</section>

<section class="card card--back">
  <div class="back-mark"></div>
  <p class="back-name">Amber Ledge Partners</p>
</section>

</body>
</html>
```